Norrell Advisory WA Business Card

Create an interesting, eye catching and colourful two sided business card. We are a business consulting operation assisting SME's improve all areas of their business. We provide consulting services to assist SME's to create a culture of continuous improvement, making a positive difference in the business. Our tag line is Small changes, big rewards. We want to create a well recognised, innovative brand that can be continued throughout our website, social media and email correspondence.

Target Market(s)

Small to Medium Enterprise Business Owners

Industry/Entity Type

Business Consultant

Contact Information for Business Card

Name of Business: Norrell Advisory - Steady steps lasting gains
Derek Holloway Ph 0407385510 Megan Holloway Ph 0407913847
Email norrelladvisorywa@mailbox-example.com
Web address TBA
FaceBook page TBA

BACKSIDE OF CARD

Providing assistance with:

• Organisation & Efficiency
• Revenue generation & Marketing
• Financial Management
• Production quality & delivery
• Systems & Process documentation
• Exit Strategy

Font styles to use
Other font styles liked:
• Calibri

Colors

Designer to choose colors to be used in the design.

Requirements
Must have
• Calibri font

```html
<!DOCTYPE html>
<html lang="en">
<head>
<meta charset="utf-8">
<title>Norrell Advisory WA – Business Card</title>
<link href="https://fonts.googleapis.com/css2?family=Carlito:wght@400;700&display=swap" rel="stylesheet">
<style>
  :root {
    --page-bg: #e9e6e1;
    --card-bg: #ffffff;
    --ink: #2b2b2b;
    --ink-soft: #555555;
    --brand-blue: #1a7fc4;
    --card-shadow: rgba(0, 0, 0, 0.18);
  }
  * { margin: 0; padding: 0; box-sizing: border-box; }
  html, body {
    width: 1200px;
    height: 1040px;
    overflow: hidden;
    background: var(--page-bg);
    font-family: "Carlito", "Calibri", sans-serif;
    color: var(--ink);
  }
  .sheet {
    position: relative;
    width: 1200px;
    height: 1040px;
  }
  .card {
    position: absolute;
    left: 160px;
    width: 880px;
    height: 489px;
    background: var(--card-bg);
    box-shadow: 0 6px 18px var(--card-shadow);
  }
  .card--front { top: 20px; }
  .card--back { top: 531px; }

  .brand-block { position: absolute; }
  .brand-name {
    font-weight: 700;
    font-size: 34px;
    letter-spacing: 1px;
    text-transform: uppercase;
    color: var(--ink);
    line-height: 1;
  }
  .brand-tagline {
    margin-top: 6px;
    font-size: 17px;
    letter-spacing: 2.5px;
    text-transform: uppercase;
    color: var(--ink-soft);
  }
  .card--front .brand-block { left: 60px; top: 230px; }

  .brand-mark {
    position: absolute;
    display: flex;
    align-items: center;
    gap: 18px;
  }
  .brand-mark__square {
    width: 64px;
    height: 64px;
    background: var(--brand-blue);
  }
  .brand-mark__name {
    font-weight: 700;
    font-size: 40px;
    color: var(--brand-blue);
    line-height: 1.05;
  }
  .card--front .brand-mark { right: 70px; top: 80px; }

  .people { position: absolute; left: 60px; top: 330px; }
  .person { margin-bottom: 14px; }
  .person__name {
    font-weight: 700;
    font-size: 32px;
    color: var(--brand-blue);
    line-height: 1;
  }
  .person__phone {
    font-weight: 700;
    font-size: 19px;
    color: var(--ink);
    margin-top: 3px;
  }

  .contacts {
    position: absolute;
    left: 430px;
    top: 360px;
    list-style: none;
  }
  .contacts li {
    display: flex;
    align-items: center;
    gap: 12px;
    font-size: 19px;
    color: var(--ink-soft);
    margin-bottom: 8px;
  }
  .contacts svg { flex: none; }

  .card--back .brand-mark { left: 90px; top: 80px; }
  .card--back .brand-mark__square { width: 40px; height: 40px; }
  .card--back .brand-mark__name { font-size: 26px; }
  .card--back .brand-block { left: 90px; top: 150px; }
  .card--back .brand-name { font-size: 30px; }
  .card--back .brand-tagline { font-size: 15px; }

  .services { position: absolute; left: 470px; top: 70px; }
  .services__title {
    font-weight: 700;
    font-size: 32px;
    color: var(--brand-blue);
    margin-bottom: 16px;
  }
  .services__list { list-style: none; }
  .services__list li {
    display: flex;
    align-items: center;
    gap: 10px;
    font-size: 21px;
    color: var(--ink);
    line-height: 1.55;
  }
  .services__bullet { color: var(--brand-blue); font-weight: 700; }
</style>
</head>
<body>
<main class="sheet">

  <section class="card card--front" aria-label="Front of business card">
    <div class="brand-mark">
      <span class="brand-mark__square"></span>
      <span class="brand-mark__name">Norrell<br>Advisory</span>
    </div>

    <div class="brand-block">
      <p class="brand-name">Norrell Advisory</p>
      <p class="brand-tagline">Steady steps lasting gains</p>
    </div>

    <div class="people">
      <div class="person">
        <p class="person__name">Derek Holloway</p>
        <p class="person__phone">0407385510</p>
      </div>
      <div class="person">
        <p class="person__name">Megan Holloway</p>
        <p class="person__phone">0407913847</p>
      </div>
    </div>

    <ul class="contacts">
      <li>
        <svg width="18" height="18" viewBox="0 0 18 18" aria-hidden="true">
          <rect width="18" height="18" rx="2" fill="#1a7fc4"/>
          <path d="M3 5h12v8H3z M3 5l6 5 6-5" fill="none" stroke="#fff" stroke-width="1.4"/>
        </svg>
        norrelladvisorywa@mailbox-example.com
      </li>
      <li>
        <svg width="18" height="18" viewBox="0 0 18 18" aria-hidden="true">
          <circle cx="9" cy="9" r="9" fill="#1a7fc4"/>
          <ellipse cx="9" cy="9" rx="3.5" ry="7" fill="none" stroke="#fff" stroke-width="1.2"/>
          <line x1="2" y1="9" x2="16" y2="9" stroke="#fff" stroke-width="1.2"/>
        </svg>
        www.norrelladvisorywa.com
      </li>
      <li>
        <svg width="18" height="18" viewBox="0 0 18 18" aria-hidden="true">
          <rect width="18" height="18" rx="2" fill="#1a7fc4"/>
        </svg>
        norrelladvisorywa
      </li>
    </ul>
  </section>

  <section class="card card--back" aria-label="Back of business card">
    <div class="brand-mark">
      <span class="brand-mark__square"></span>
      <span class="brand-mark__name">Norrell Advisory</span>
    </div>

    <div class="brand-block">
      <p class="brand-name">Norrell Advisory</p>
      <p class="brand-tagline">Steady steps lasting gains</p>
    </div>

    <div class="services">
      <h2 class="services__title">Providing assistance with</h2>
      <ul class="services__list">
        <li><span class="services__bullet">✱</span>Organisation &amp; Efficiency</li>
        <li><span class="services__bullet">✱</span>Revenue generation &amp; Marketing</li>
        <li><span class="services__bullet">✱</span>Financial Management</li>
        <li><span class="services__bullet">✱</span>Production quality &amp; delivery</li>
        <li><span class="services__bullet">✱</span>Systems &amp; Process documentation</li>
        <li><span class="services__bullet">✱</span>Exit Strategy</li>
      </ul>
    </div>
  </section>

</main>
</body>
</html>
```